Finiding oppertunites in Real Estate 6.15.20

size of ad 7” x 9.6”
1-I like the ad to stand out and attract people's attention.
2-you should be able to see the text of the ad clearly .. see the attachment anything in yellow is instructions.
3-the list of topics should not be the main part of the ad
4-if you decide you want a picture or vector of a person .. (you decide)
then it should be a white male about 25-30 years old wearing a solid white or blue shirt and not long hair.
5-leave 1 inch for footer
see attachment
Good luck

Target Market(s)

potential male students 25-35 years of age

Industry/Entity Type

Education

Requirements
Must have
• will stand out and people would want to see it.
should be able to read the words of ad
Nice to have
• how to make money in real estate on one line

```html
<!DOCTYPE html>
<html lang="en">
<head>
<meta charset="utf-8">
<title>Real Estate Course Flyer</title>
<link rel="stylesheet" href="https://fonts.googleapis.com/css2?family=Montserrat:wght@500;600;700;800&family=Oswald:wght@500;600;700&display=swap">
<style>
  :root {
    --blue: #0b6cbf;
    --blue-deep: #07508f;
    --navy: #0c4a8a;
    --orange: #e8890b;
    --ink: #111111;
    --panel: #f2f3f5;
    --white: #ffffff;
    --text: #1d1d1d;
  }
  * { margin: 0; padding: 0; box-sizing: border-box; }
  html, body { width: 926px; height: 1200px; overflow: hidden; background: var(--white); }
  .flyer { position: relative; width: 926px; height: 1200px; overflow: hidden; font-family: "Montserrat", sans-serif; background: var(--white); }

  .title-band { position: absolute; left: 0; top: 0; width: 926px; height: 129px; background: var(--blue); display: flex; align-items: center; justify-content: center; }
  .title-band h1 { color: var(--white); font-weight: 700; font-size: 64px; letter-spacing: 1px; line-height: 1; }

  .hero { position: absolute; left: 0; top: 129px; width: 926px; height: 706px; background: linear-gradient(135deg, #f7f7f8 0%, #ffffff 45%, #eceef1 100%); }

  .portrait { position: absolute; left: 575px; top: 247px; width: 351px; height: 588px; border-radius: 60px 0 0 0; background: linear-gradient(180deg, #e3e7ec 0%, #9fb4d3 25%, #2f5fa8 55%, #1e4d96 100%); }

  .headline { position: absolute; left: 62px; top: 152px; width: 801px; text-align: center; white-space: nowrap; font-family: "Oswald", sans-serif; font-weight: 700; font-size: 55px; line-height: 1; color: var(--ink); letter-spacing: -0.5px; }
  .headline .accent { color: var(--orange); }
  .headline .key { color: var(--blue); }

  .tagline { position: absolute; left: 62px; top: 290px; font-family: "Oswald", sans-serif; font-weight: 600; font-size: 50px; line-height: 62px; white-space: nowrap; }
  .tagline .line-blue { color: var(--blue); display: block; }
  .tagline .line-orange { color: var(--orange); display: block; }

  .badge { position: absolute; left: 106px; top: 524px; width: 296px; height: 140px; }
  .badge-text-remote { position: absolute; left: 140px; top: 552px; color: var(--white); font-weight: 700; font-size: 30px; transform: rotate(-4deg); letter-spacing: 0.5px; }
  .badge-text-sessions { position: absolute; left: 150px; top: 594px; color: var(--white); font-family: "Oswald", sans-serif; font-weight: 700; font-size: 37px; line-height: 1; }

  .pill { position: absolute; color: var(--white); font-weight: 700; display: flex; align-items: center; }
  .pill-start { left: 119px; top: 671px; width: 244px; height: 30px; background: var(--navy); font-size: 19px; padding-left: 24px; letter-spacing: 0.3px; }
  .pill-count { left: 105px; top: 700px; width: 192px; height: 27px; background: var(--orange); font-size: 18px; padding-left: 36px; font-weight: 600; }
  .pill-night { left: 140px; top: 725px; width: 255px; height: 30px; background: var(--blue); font-size: 20px; padding-left: 22px; }

  .audience-band { position: absolute; left: 0; top: 835px; width: 926px; height: 54px; background: var(--orange); color: var(--white); font-weight: 500; font-size: 22px; display: flex; align-items: center; justify-content: center; }

  .topics { position: absolute; left: 0; top: 889px; width: 926px; height: 141px; }
  .topic-col { position: absolute; top: 16px; list-style: none; }
  .topic-col li { font-size: 17px; font-weight: 500; color: var(--text); height: 26.5px; display: flex; align-items: center; gap: 8px; }
  .topic-col svg { width: 12px; height: 12px; flex: none; }
  .col-1 { left: 63px; } .col-2 { left: 379px; } .col-3 { left: 703px; }
  .divider { position: absolute; top: 22px; width: 1px; height: 97px; background: var(--orange); }
  .divider-1 { left: 322px; } .divider-2 { left: 645px; }

  .footer { position: absolute; left: 0; top: 1030px; width: 926px; height: 125px; background: var(--panel); }
  .footer-left { position: absolute; left: 0; top: 0; width: 277px; height: 125px; background: var(--blue-deep); clip-path: polygon(0 0, 100% 0, 93.5% 100%, 0 100%); }
  .footer-right { position: absolute; right: 0; top: 0; width: 267px; height: 125px; background: var(--blue); clip-path: polygon(6% 0, 100% 0, 100% 100%, 0 100%); }
  .org-name { position: absolute; left: 34px; top: 42px; color: var(--white); font-weight: 700; font-size: 19px; line-height: 1.15; }
  .org-sub { position: absolute; left: 34px; top: 90px; color: var(--white); font-size: 10px; font-weight: 500; letter-spacing: 0.3px; }
  .contact { position: absolute; left: 0; top: 0; font-size: 13px; color: var(--navy); font-weight: 500; }
  .contact-row { position: absolute; display: flex; align-items: center; gap: 6px; white-space: nowrap; }
  .contact-row svg { width: 19px; height: 19px; flex: none; }
  .contact-row strong { font-weight: 700; }
  .row-address { left: 283px; top: 16px; }
  .row-web { left: 281px; top: 45px; }
  .row-phone { left: 461px; top: 45px; }
  .row-mail { left: 279px; top: 74px; }
  .sponsor-label { position: absolute; right: 22px; top: 22px; color: var(--white); font-size: 12.5px; font-weight: 500; }
  .sponsor-name { position: absolute; right: 22px; top: 48px; color: var(--white); font-size: 22px; font-weight: 600; line-height: 1.05; text-align: right; }

  .credit { position: absolute; left: 0; top: 1155px; width: 926px; height: 45px; display: flex; align-items: center; justify-content: center; font-weight: 700; font-size: 16px; color: var(--ink); }
</style>
</head>
<body>
<main class="flyer">
  <header class="title-band"><h1>REAL ESTATE COURSE</h1></header>

  <section class="hero" aria-hidden="true"></section>

  <div class="portrait" role="img" aria-label="Photo of a smiling young businessman in a blue suit and tie"></div>

  <h2 class="headline">HOW TO <span class="accent">MAKE MONEY</span> IN <span class="key">REAL ESTATE?</span></h2>

  <p class="tagline">
    <span class="line-blue">Investing in Knowledge</span>
    <span class="line-orange">Opens up Opportunities</span>
  </p>

  <svg class="badge" viewBox="0 0 296 140" aria-hidden="true">
    <polygon points="110,6 294,44 176,106" fill="none" stroke="#b9bcc2" stroke-width="2"/>
    <polygon points="0,20 262,4 249,95 13,100" fill="#e8890b"/>
    <polygon points="34,60 230,46 224,118 36,120" fill="#0b6cbf"/>
  </svg>
  <div class="badge-text-remote">REMOTE</div>
  <div class="badge-text-sessions">SESSIONS</div>

  <div class="pill pill-start">STARTING JULY 8</div>
  <div class="pill pill-count">12 SESSIONS</div>
  <div class="pill pill-night">Wednesday Nights</div>

  <div class="audience-band">For those who have started or would like to enter into Real Estate</div>

  <section class="topics">
    <ul class="topic-col col-1">
      <li><svg viewBox="0 0 12 12"><circle cx="6" cy="6" r="5.2" fill="none" stroke="#e8890b" stroke-width="1.2"/><path d="M3.5 6.2l1.7 1.6 3.3-3.4" fill="none" stroke="#e8890b" stroke-width="1.2"/></svg>Single-family</li>
      <li><svg viewBox="0 0 12 12"><circle cx="6" cy="6" r="5.2" fill="none" stroke="#e8890b" stroke-width="1.2"/><path d="M3.5 6.2l1.7 1.6 3.3-3.4" fill="none" stroke="#e8890b" stroke-width="1.2"/></svg>Multifamily</li>
      <li><svg viewBox="0 0 12 12"><circle cx="6" cy="6" r="5.2" fill="none" stroke="#e8890b" stroke-width="1.2"/><path d="M3.5 6.2l1.7 1.6 3.3-3.4" fill="none" stroke="#e8890b" stroke-width="1.2"/></svg>Management</li>
      <li><svg viewBox="0 0 12 12"><circle cx="6" cy="6" r="5.2" fill="none" stroke="#e8890b" stroke-width="1.2"/><path d="M3.5 6.2l1.7 1.6 3.3-3.4" fill="none" stroke="#e8890b" stroke-width="1.2"/></svg>Real Estate Concepts</li>
    </ul>
    <span class="divider divider-1"></span>
    <ul class="topic-col col-2">
      <li><svg viewBox="0 0 12 12"><circle cx="6" cy="6" r="5.2" fill="none" stroke="#e8890b" stroke-width="1.2"/><path d="M3.5 6.2l1.7 1.6 3.3-3.4" fill="none" stroke="#e8890b" stroke-width="1.2"/></svg>Real Estate law</li>
      <li><svg viewBox="0 0 12 12"><circle cx="6" cy="6" r="5.2" fill="none" stroke="#e8890b" stroke-width="1.2"/><path d="M3.5 6.2l1.7 1.6 3.3-3.4" fill="none" stroke="#e8890b" stroke-width="1.2"/></svg>Investment properties</li>
      <li><svg viewBox="0 0 12 12"><circle cx="6" cy="6" r="5.2" fill="none" stroke="#e8890b" stroke-width="1.2"/><path d="M3.5 6.2l1.7 1.6 3.3-3.4" fill="none" stroke="#e8890b" stroke-width="1.2"/></svg>Foreclosures</li>
      <li><svg viewBox="0 0 12 12"><circle cx="6" cy="6" r="5.2" fill="none" stroke="#e8890b" stroke-width="1.2"/><path d="M3.5 6.2l1.7 1.6 3.3-3.4" fill="none" stroke="#e8890b" stroke-width="1.2"/></svg>Rehab</li>
    </ul>
    <span class="divider divider-2"></span>
    <ul class="topic-col col-3">
      <li><svg viewBox="0 0 12 12"><circle cx="6" cy="6" r="5.2" fill="none" stroke="#e8890b" stroke-width="1.2"/><path d="M3.5 6.2l1.7 1.6 3.3-3.4" fill="none" stroke="#e8890b" stroke-width="1.2"/></svg>Short sales</li>
      <li><svg viewBox="0 0 12 12"><circle cx="6" cy="6" r="5.2" fill="none" stroke="#e8890b" stroke-width="1.2"/><path d="M3.5 6.2l1.7 1.6 3.3-3.4" fill="none" stroke="#e8890b" stroke-width="1.2"/></svg>Development</li>
      <li><svg viewBox="0 0 12 12"><circle cx="6" cy="6" r="5.2" fill="none" stroke="#e8890b" stroke-width="1.2"/><path d="M3.5 6.2l1.7 1.6 3.3-3.4" fill="none" stroke="#e8890b" stroke-width="1.2"/></svg>Finical modeling</li>
      <li><svg viewBox="0 0 12 12"><circle cx="6" cy="6" r="5.2" fill="none" stroke="#e8890b" stroke-width="1.2"/><path d="M3.5 6.2l1.7 1.6 3.3-3.4" fill="none" stroke="#e8890b" stroke-width="1.2"/></svg>Due Diligence</li>
    </ul>
  </section>

  <footer class="footer">
    <div class="footer-left"></div>
    <div class="org-name">Northway<br>Career Center</div>
    <div class="org-sub">A NON-PROFIT COMMUNITY SERVICE</div>

    <div class="contact">
      <div class="contact-row row-address">
        <svg viewBox="0 0 20 20"><circle cx="10" cy="10" r="9" fill="none" stroke="#0b6cbf" stroke-width="1.2"/><path d="M10 4.5a3.5 3.5 0 0 0-3.5 3.5c0 2.6 3.5 6.5 3.5 6.5s3.5-3.9 3.5-6.5A3.5 3.5 0 0 0 10 4.5z" fill="none" stroke="#0b6cbf" stroke-width="1.3"/><circle cx="10" cy="8" r="1.2" fill="#0b6cbf"/></svg>
        <span>Eastfield - Milford - Lakeside, <strong>Main Branch</strong></span>
      </div>
      <div class="contact-row row-web">
        <svg viewBox="0 0 20 20"><circle cx="10" cy="10" r="9" fill="none" stroke="#0b6cbf" stroke-width="1.2"/><circle cx="10" cy="10" r="5" fill="none" stroke="#0b6cbf" stroke-width="1.1"/><path d="M5 10h10M10 5c-2 2.8-2 7.2 0 10M10 5c2 2.8 2 7.2 0 10" fill="none" stroke="#0b6cbf" stroke-width="1"/></svg>
        <span>www.nwcareers.org</span>
      </div>
      <div class="contact-row row-phone">
        <svg viewBox="0 0 20 20"><circle cx="10" cy="10" r="9" fill="none" stroke="#0b6cbf" stroke-width="1.2"/><path d="M7 5.5l1.6 2.2-1 1.2c.7 1.4 1.8 2.5 3.2 3.2l1.2-1 2.2 1.6-.9 1.8c-3.6-.3-6.8-3.5-7.1-7.1z" fill="#0b6cbf"/></svg>
        <span>555 010 0148 x 206</span>
      </div>
      <div class="contact-row row-mail">
        <svg viewBox="0 0 20 20"><circle cx="10" cy="10" r="9" fill="none" stroke="#0b6cbf" stroke-width="1.2"/><rect x="5.5" y="7" width="9" height="6.5" rx="1" fill="#0b6cbf"/><path d="M5.8 7.4L10 10.6l4.2-3.2" fill="none" stroke="#ffffff" stroke-width="1"/></svg>
        <span>info@nwcareers.org</span>
      </div>
    </div>

    <div class="footer-right"></div>
    <div class="sponsor-label">sponsored by</div>
    <div class="sponsor-name">Harborline<br>Capital</div>
  </footer>

  <div class="credit">Northway is sponsored in part by the Ellison Rowe foundation</div>
</main>
</body>
</html>
```